Brightwave Reach - Business Card

We need a business card for a Social Media Marketing company that specializes in online marketing for small businesses in Canada using common Social Media platforms such as Pixlora, Chatterly, Blinkpost & Quibber.

I have uploaded a copy of our logo which I would like utilized in the business card. We would like the business card to be modern yet classy design.

Our website is www.brightwavereach.ca

Industry/Entity Type

Marketing

Contact Information for Business Card

Email: info@brightwavereach.ca
Website: www.brightwavereach.ca
Telephone: 604-555-0193

Colors

Designer to choose colors to be used in the design.

Requirements
Must have
• Social Media icons on reverse
• Please add some designs with color.

```html
<!DOCTYPE html>
<html lang="en">
<head>
<meta charset="utf-8">
<title>Brightwave Reach – Business Card</title>
<link href="https://fonts.googleapis.com/css2?family=Roboto+Condensed:wght@400;700&display=swap" rel="stylesheet">
<style>
  :root {
    --stage: #0b0b0b;
    --back-dark: #2e2f2f;
    --back-light: #3f4243;
    --front-paper: #f8f6f1;
    --front-band: #dcdcda;
    --front-band-light: #e7e7e4;
    --ink: #3a3a3a;
    --ink-soft: #4a4a4a;
    --white: #ffffff;
  }
  html, body {
    margin: 0;
    padding: 0;
    width: 1200px;
    height: 1000px;
    overflow: hidden;
    background: var(--stage);
    font-family: "Roboto Condensed", "Arial Narrow", sans-serif;
  }
  .canvas {
    position: relative;
    width: 1200px;
    height: 1000px;
  }
  .card {
    position: absolute;
    top: 350px;
    width: 525px;
    height: 300px;
    overflow: hidden;
    box-shadow: 0 10px 30px rgba(0,0,0,0.6);
  }
  .card-back { left: 50px; background: var(--back-dark); }
  .card-front { left: 625px; background: var(--front-paper); }
  .card-shape { position: absolute; inset: 0; }

  /* back */
  .handle {
    position: absolute;
    left: 0; right: 0;
    top: 112px;
    text-align: center;
    color: var(--white);
    font-weight: 700;
    font-size: 26px;
    letter-spacing: 0.5px;
    margin: 0;
  }
  .social-list {
    position: absolute;
    left: 0; right: 0;
    top: 160px;
    display: flex;
    justify-content: center;
    gap: 16px;
    margin: 0; padding: 0;
    list-style: none;
  }
  .social-item {
    display: flex;
    align-items: center;
    gap: 5px;
    color: var(--white);
    font-size: 12px;
    letter-spacing: 0.3px;
  }
  .social-dot {
    width: 14px; height: 14px;
    border: 1.5px solid var(--white);
    border-radius: 50%;
    box-sizing: border-box;
  }

  /* front */
  .person {
    position: absolute;
    left: 30px; top: 26px;
    margin: 0;
    color: var(--ink);
  }
  .person-name {
    display: block;
    font-weight: 700;
    font-size: 22px;
    letter-spacing: 0.5px;
  }
  .person-role {
    display: block;
    font-size: 16px;
    letter-spacing: 0.5px;
    line-height: 1.05;
  }
  .contact {
    position: absolute;
    left: 30px; top: 128px;
    margin: 0;
    font-style: normal;
    color: var(--ink-soft);
    font-size: 15px;
    line-height: 21px;
    letter-spacing: 0.3px;
  }
  .brand {
    position: absolute;
    right: 34px; top: 196px;
    display: flex;
    align-items: center;
    gap: 8px;
    color: var(--ink);
    font-weight: 700;
    font-size: 24px;
    letter-spacing: 0.5px;
  }
  .brand-square {
    width: 16px; height: 16px;
    background: var(--ink);
  }
</style>
</head>
<body>
<main class="canvas">

  <section class="card card-back" aria-label="Business card reverse">
    <svg class="card-shape" viewBox="0 0 525 300" aria-hidden="true">
      <polygon points="300,0 525,0 525,300 115,300" fill="var(--back-light)"/>
    </svg>
    <p class="handle">/BRIGHTWAVEREACH</p>
    <ul class="social-list">
      <li class="social-item"><span class="social-dot"></span>Quibber</li>
      <li class="social-item"><span class="social-dot"></span>Blinkpost</li>
      <li class="social-item"><span class="social-dot"></span>Pixlora</li>
      <li class="social-item"><span class="social-dot"></span>Chatterly</li>
    </ul>
  </section>

  <section class="card card-front" aria-label="Business card front">
    <svg class="card-shape" viewBox="0 0 525 300" aria-hidden="true">
      <rect x="0" y="100" width="500" height="170" fill="var(--front-band)"/>
      <polygon points="360,170 500,170 500,270 250,270" fill="var(--front-band-light)"/>
    </svg>
    <h1 class="person">
      <span class="person-name">DANIEL MOREAU</span>
      <span class="person-role">MANAGER</span>
    </h1>
    <address class="contact">
      604-555-0193<br>
      INFO@BRIGHTWAVEREACH.CA<br>
      WWW.BRIGHTWAVEREACH.CA
    </address>
    <div class="brand"><span class="brand-square"></span>BRIGHTWAVE REACH</div>
  </section>

</main>
</body>
</html>
```